Business Card Design

Hi I need a business card designed, we already have the business name logo artwork and would like some concept ideas for the Bus Card layout.
On the back of the card i want to include the products and services that we offer.
We are a Plastics Sheeting manufacture based in Perth Australia.

                                       

We need a BC design for a company called Tarvo Plastics based in Perth Australia.

We supply from DIY to Trade & Industrial  Engineering Markets.

We specialise in:

·         Cut to size panels  (all shapes and sizes)

·         Plastics fabrication & Welding

·         Custom Designs

·         Plastic Repairs

·         PVC Pipe Slotting & PVC Pipe Threading

·         Supplier of all types of engineering plastics and profiles.

Including:           Acrylic / Clarvene

                               Polycarbonate / Dorvil

                               Prismatic Light Diffuser

                               Vantrib

                               HDPE / UHMWPE

                               PVC / PVC Foam

                               Nylon

                               HIPS

```html
<!DOCTYPE html>
<html lang="en">
<head>
<meta charset="utf-8">
<title>Tarvo Plastics – Business Card</title>
<link href="https://fonts.googleapis.com/css2?family=Arimo:ital,wght@0,400;0,700;1,700&display=swap" rel="stylesheet">
<style>
  :root {
    --backdrop: #e6e3df;
    --card-white: #ffffff;
    --brand-red: #d0062c;
    --brand-navy: #1b2a5c;
    --link-blue: #2a8fd0;
    --text-white: #ffffff;
    --shadow: rgba(0, 0, 0, 0.18);
    --ribbon-blue: rgba(120, 180, 225, 0.35);
    --ribbon-yellow: rgba(245, 215, 120, 0.35);
    --ribbon-red: rgba(215, 110, 120, 0.25);
    --ribbon-green: rgba(160, 200, 140, 0.3);
  }
  * { margin: 0; padding: 0; box-sizing: border-box; }
  html, body {
    width: 1200px; height: 631px; overflow: hidden;
    background: var(--backdrop);
    font-family: "Arimo", Arial, sans-serif;
  }
  .canvas {
    position: relative; width: 1200px; height: 631px;
    display: flex; align-items: center; justify-content: center; gap: 40px;
  }
  .card {
    position: relative; width: 520px; height: 297px;
    box-shadow: 0 6px 18px var(--shadow);
    overflow: hidden;
  }

  /* Back of card */
  .card-back { background: var(--brand-red); color: var(--text-white); }
  .back-brand {
    position: absolute; left: 0; top: 0; width: 82px; height: 297px;
    display: flex; align-items: center; justify-content: center;
  }
  .back-brand span {
    display: block; transform: rotate(-90deg); white-space: nowrap;
    font-weight: 700; font-size: 30px; color: var(--text-white);
  }
  .back-content {
    position: absolute; left: 100px; top: 34px; right: 18px;
    font-size: 10px; line-height: 1.62;
  }
  .back-intro { margin-bottom: 8px; }
  .back-columns { display: flex; gap: 22px; }
  .services { flex: 1 1 auto; }
  .materials { flex: 0 0 118px; }
  .col-heading { font-weight: 700; }
  .materials .col-heading { font-style: italic; }
  .services ul, .materials ul { list-style: none; }
  .services li::before { content: "• "; }
  .materials li { font-weight: 700; }

  /* Front of card */
  .card-front { background: var(--card-white); color: var(--brand-navy); }
  .ribbon-decor {
    position: absolute; right: -40px; top: -20px; width: 330px; height: 340px;
    background: linear-gradient(200deg, var(--ribbon-red) 0%, var(--ribbon-green) 25%, var(--ribbon-blue) 50%, var(--ribbon-yellow) 75%, rgba(255,255,255,0) 100%);
    border-radius: 60% 0 0 100%;
  }
  .front-brand {
    position: relative; position: absolute; left: 34px; top: 52px;
    font-weight: 700; font-size: 38px; color: var(--brand-navy);
  }
  .contact {
    position: absolute; left: 262px; top: 120px;
    font-size: 13px; line-height: 1.3; font-style: normal;
  }
  .contact strong { font-weight: 700; }
  .contact .email { color: var(--link-blue); }
  .contact .legal { font-size: 7px; margin-top: 3px; padding-left: 40px; }
  .person {
    position: absolute; left: 34px; top: 212px;
    font-size: 14px; line-height: 1.35;
  }
  .person strong { font-weight: 700; }
</style>
</head>
<body>
<main class="canvas">
  <section class="card card-back" aria-label="Card back">
    <div class="back-brand"><span>Tarvo Plastics</span></div>
    <div class="back-content">
      <p class="back-intro">We supply from DIY to Trade &amp; Industrial Engineering Markets.</p>
      <div class="back-columns">
        <div class="services">
          <p class="col-heading">We specialise in:</p>
          <ul>
            <li>Cut to size panels (all shapes and sizes)</li>
            <li>Plastics fabrication &amp; Welding</li>
            <li>Custom Designs</li>
            <li>Plastic Repairs</li>
            <li>PVC Pipe Slotting &amp; PVC Pipe Threading</li>
            <li>Supplier of all types of engineering plastics and profiles</li>
          </ul>
        </div>
        <div class="materials">
          <p class="col-heading">Including</p>
          <ul>
            <li>Acrylic / Clarvene</li>
            <li>Polycarbonate / Dorvil</li>
            <li>Prismatic Light Diffuser</li>
            <li>Vantrib</li>
            <li>HDPE / UHMWPE</li>
            <li>PVC / PVC Foam</li>
            <li>Nylon</li>
            <li>HIPS</li>
          </ul>
        </div>
      </div>
    </div>
  </section>

  <section class="card card-front" aria-label="Card front">
    <div class="ribbon-decor" role="img" aria-label="Faint multicoloured sweeping ribbon decoration"></div>
    <p class="front-brand">Tarvo Plastics</p>
    <address class="contact">
      <p>Unit 4/18 Harlow</p>
      <p>Circuit Brenton Vale WA 6088</p>
      <p>Ph: <strong>08 9000 4811</strong> Fax: <strong>08 9000 4822</strong></p>
      <p>E: <span class="email">sales@tarvoplastics.com.au</span></p>
      <p>PO Box 2270 Brenton Vale DC WA 6089</p>
      <p class="legal">KELMOR WA Pty Ltd T/A Tarvo Plastics ABN: TBA</p>
    </address>
    <div class="person">
      <p><strong>Name</strong>| 1234 123 123</p>
      <p><strong>Manager</strong></p>
    </div>
  </section>
</main>
</body>
</html>
```